Bramblewood Card Company Business Cards

We are a trading card store with Glimmorax, sports and other TCG cards, we need a business card design that encompasses a clean cut, modern style with a retro flare. website is bramblewoodcardco.com for reference. Can utilize a comic book era feel or a more modern outdoor feel to utilize the "Pacific Northwest" elements of tress, mountains, etc.

Industry/Entity Type

Trading cards and collectibles

Contact Information for Business Card

business name, email address, phone number, name, owner job title

Font styles to use
Sans Serif

```html
<!DOCTYPE html>
<html lang="en">
<head>
<meta charset="utf-8">
<title>Bramblewood Card Company – Business Card</title>
<link rel="stylesheet" href="https://fonts.googleapis.com/css2?family=Montserrat:wght@400;500;800&display=swap">
<style>
  :root {
    --backdrop: #c4c4c4;
    --card-white: #ffffff;
    --card-grey: #767676;
    --brand-cyan: #22bde0;
    --ink: #2b2b2b;
    --logo-grey: #6b6b6b;
  }
  * { box-sizing: border-box; margin: 0; padding: 0; }
  html, body {
    width: 1200px; height: 815px; overflow: hidden;
    background: var(--backdrop);
    font-family: "Montserrat", sans-serif;
  }
  .stage {
    position: relative; width: 1200px; height: 815px;
    display: flex; align-items: center; justify-content: center; gap: 40px;
  }
  .card {
    position: relative; width: 550px; height: 314px;
    border-radius: 22px;
    box-shadow: 0 4px 0 var(--brand-cyan), 0 14px 28px rgba(0,0,0,0.25);
    overflow: hidden;
  }
  .card--front { background: var(--card-white); color: var(--ink); }
  .card--back {
    background: var(--card-grey);
    display: flex; align-items: center; justify-content: center;
  }
  .brand-name {
    position: absolute; top: 42px; right: 40px;
    width: 190px; text-align: center;
    font-weight: 800; font-size: 19px; line-height: 1.15;
    letter-spacing: 1px; text-transform: uppercase;
    color: var(--logo-grey);
  }
  .brand-name--large {
    position: static; width: auto;
    font-size: 34px; line-height: 1.15; letter-spacing: 2px;
    color: var(--card-white);
  }
  .holder { position: absolute; left: 40px; top: 128px; }
  .holder__name {
    font-weight: 800; font-size: 27px; letter-spacing: 1px;
    color: var(--brand-cyan); text-transform: uppercase; line-height: 1;
  }
  .holder__title {
    font-weight: 500; font-size: 13px; letter-spacing: 0.5px;
    text-transform: uppercase; margin-top: 4px;
  }
  .contact { list-style: none; margin-top: 12px; }
  .contact__item {
    display: flex; align-items: center; gap: 8px;
    font-size: 13.5px; line-height: 22px;
  }
  .contact__icon { width: 12px; height: 12px; flex: none; }
  .rule {
    position: absolute; left: 40px; right: 40px; top: 262px;
    height: 1px; background: var(--brand-cyan);
  }
  .address {
    position: absolute; left: 40px; top: 274px;
    font-size: 13.5px;
  }
</style>
</head>
<body>
<main class="stage">
  <section class="card card--front" aria-label="Business card front">
    <div class="brand-name">Bramblewood Card Company</div>
    <div class="holder">
      <h1 class="holder__name">Rowan Ellery</h1>
      <p class="holder__title">Manager</p>
      <ul class="contact">
        <li class="contact__item">
          <svg class="contact__icon" viewBox="0 0 12 12" aria-hidden="true"><path d="M2.5 1 L4.5 1 L5.2 3.6 L4 4.6 C4.7 6 6 7.3 7.4 8 L8.4 6.8 L11 7.5 L11 9.5 C11 10.3 10.3 11 9.5 11 C5 11 1 7 1 2.5 C1 1.7 1.7 1 2.5 1 Z" fill="var(--brand-cyan)"/></svg>
          (555)014-6789
        </li>
        <li class="contact__item">
          <svg class="contact__icon" viewBox="0 0 12 12" aria-hidden="true"><rect x="0.5" y="2" width="11" height="8" rx="1" fill="var(--brand-cyan)"/><path d="M1 2.8 L6 6.6 L11 2.8" stroke="#fff" stroke-width="1" fill="none"/></svg>
          info@youremail.com
        </li>
        <li class="contact__item">
          <svg class="contact__icon" viewBox="0 0 12 12" aria-hidden="true"><circle cx="6" cy="6" r="5.5" fill="var(--brand-cyan)"/><path d="M0.5 6 H11.5 M6 0.5 V11.5 M6 0.5 C3 3.5 3 8.5 6 11.5 M6 0.5 C9 3.5 9 8.5 6 11.5" stroke="#fff" stroke-width="0.7" fill="none"/></svg>
          www.yourwebsite.com
        </li>
      </ul>
    </div>
    <div class="rule"></div>
    <p class="address">2240 Alder Ridge Road 48, Your Country, WA 98011</p>
  </section>

  <section class="card card--back" aria-label="Business card back">
    <div class="brand-name brand-name--large">Bramblewood<br>Card Company</div>
  </section>
</main>
</body>
</html>
```